Stylish Business Cards Wanted

- DOUBLE SIDED Design Required -

High end, edgy cards for a corporate and personal stylist. Must include logo,
Name: Belinda Harwick
Title: Director and Stylist
telephone : +61 8 7142 5809
email: belinda@theloombriefing.example
website: theloombriefing.example
Tag: Corporate Workwear & Uniform Specialist | Personal Stylist
Would like nice icons for telephone, email, website

Target Market(s)

Businesses wanting stylish uniforms, people wanting stylish wardrobes

Industry/Entity Type

Corporate Workwear Stylist

Contact Information for Business Card

I would like black, white and gold foiling incorporated in the design - possibly a touch of the other colours on my branding guide attached Name: Belinda Harwick Title: Director and Stylist telephone : +61 8 7142 5809 email: belinda@theloombriefing.example website: theloombriefing.example Tag: Corporate Workwear & Uniform Specialist | Personal Stylist Would like nice icons for telephone, email, website

Font styles to use
Other font styles liked:
• Raleway

Colors

Designer to choose colors to be used in the design.

Requirements
Must have
• Gold foil accents

```html
<!DOCTYPE html>
<html lang="en">
<head>
<meta charset="UTF-8">
<title>Belinda Harwick — Business Card</title>
<link rel="stylesheet" href="https://fonts.googleapis.com/css2?family=Roboto:wght@400;500&family=Dancing+Script:wght@500&display=swap">
<style>
  :root {
    --backdrop: #e7e3de;
    --card: #f6f4f1;
    --card-edge: #e9e5df;
    --ink: #1c1f2b;
    --navy: #1b2030;
    --gold: #c79f4b;
    --gold-light: #e3c47a;
    --gold-deep: #b58a35;
  }
  * { margin: 0; padding: 0; box-sizing: border-box; }
  html, body {
    width: 1200px;
    height: 1054px;
    overflow: hidden;
    background: var(--backdrop);
    font-family: "Roboto", Arial, sans-serif;
  }
  .card {
    position: absolute;
    left: 100px;
    top: 224px;
    width: 1000px;
    height: 605px;
    border-radius: 22px;
    background: linear-gradient(160deg, #fbfaf8 0%, var(--card) 55%, var(--card-edge) 100%);
    box-shadow: 0 18px 40px rgba(40, 32, 20, 0.14);
    overflow: hidden;
  }
  .holder-name {
    position: absolute;
    left: 72px;
    top: 132px;
    font-family: "Dancing Script", cursive;
    font-weight: 500;
    font-size: 50px;
    color: var(--gold);
    line-height: 1;
  }
  .holder-title {
    position: absolute;
    left: 74px;
    top: 201px;
    font-size: 25px;
    color: var(--ink);
  }
  .contact-list {
    position: absolute;
    left: 74px;
    top: 282px;
    list-style: none;
  }
  .contact-item {
    display: flex;
    align-items: center;
    height: 41.5px;
    font-size: 25px;
    color: var(--ink);
  }
  .contact-icon {
    width: 24px;
    height: 24px;
    margin-right: 19px;
    flex: none;
  }
  .brand-name {
    position: absolute;
    left: 548px;
    top: 188px;
    width: 380px;
    text-align: center;
    font-weight: 500;
    font-size: 64px;
    line-height: 1.05;
    color: var(--navy);
    letter-spacing: 0.5px;
  }
  .tag-band {
    position: absolute;
    left: 0;
    bottom: 0;
    width: 1000px;
    height: 66px;
  }
  .tagline {
    position: absolute;
    left: 0;
    bottom: 16px;
    width: 1000px;
    text-align: center;
    font-size: 25px;
    color: var(--ink);
  }
</style>
</head>
<body>
  <section class="card">
    <h1 class="holder-name">Belinda Harwick</h1>
    <p class="holder-title">Director and Stylist</p>

    <ul class="contact-list">
      <li class="contact-item">
        <svg class="contact-icon" viewBox="0 0 24 24" fill="none" stroke="var(--gold)" stroke-width="1.6">
          <circle cx="12" cy="12" r="10.5"/>
          <path d="M8.3 6.8l1.6-.3 1.2 2.6-1.1 1c.6 1.4 1.6 2.5 3 3.1l1-1.1 2.6 1.2-.3 1.6c-.2.6-.8.9-1.4.9-3.9-.4-7-3.5-7.4-7.4 0-.6.3-1.2.9-1.4z"/>
        </svg>
        +61 8 7142 5809
      </li>
      <li class="contact-item">
        <svg class="contact-icon" viewBox="0 0 24 24" fill="none" stroke="var(--gold)" stroke-width="1.6">
          <rect x="2" y="5" width="20" height="14" rx="1"/>
          <path d="M2.5 5.5l9.5 8 9.5-8"/>
        </svg>
        belinda@theloombriefing.example
      </li>
      <li class="contact-item">
        <svg class="contact-icon" viewBox="0 0 24 24" fill="none" stroke="var(--gold)" stroke-width="1.6">
          <circle cx="12" cy="12" r="10"/>
          <ellipse cx="12" cy="12" rx="4.3" ry="10"/>
          <path d="M2 12h20M4 6.5h16M4 17.5h16"/>
        </svg>
        www.theloombriefing.example
      </li>
    </ul>

    <p class="brand-name">The Loom<br>Briefing</p>

    <svg class="tag-band" viewBox="0 0 1000 66" preserveAspectRatio="none" aria-hidden="true">
      <defs>
        <linearGradient id="goldFoil" x1="0" y1="0" x2="1" y2="0">
          <stop offset="0" stop-color="var(--gold-deep)"/>
          <stop offset="0.35" stop-color="var(--gold-light)"/>
          <stop offset="0.65" stop-color="var(--gold)"/>
          <stop offset="1" stop-color="var(--gold-deep)"/>
        </linearGradient>
      </defs>
      <rect x="0" y="45" width="1000" height="21" fill="var(--navy)"/>
      <path d="M100 0 H900 L938 66 H62 Z" fill="url(#goldFoil)"/>
    </svg>
    <p class="tagline">Corporate Workwear &amp; Uniform Specialist &nbsp;|&nbsp; Personal Stylist</p>
  </section>
</body>
</html>
```